Kettleby Twins Playing Cards

We are wanting a cool design for a playing card that includes our logo(s). I will attach our two logos, we are open to using either one of them or another version of them. I will also attach some pictures of card decks to use for inspiration. These are just decks that we have seen from other artists that we liked. We are located in West Texas so although not necessary, a Sotol or Agave or cactus or quail (bird) or some sort of sunset would pay homage to our surroundings. I realize the examples are all very different, but those are just some decks that we like! Thank you!

```html
<!DOCTYPE html>
<html lang="en">
<head>
<meta charset="utf-8">
<title>Kettleby Twins Playing Cards</title>
<link rel="stylesheet" href="https://fonts.googleapis.com/css2?family=Alfa+Slab+One&family=Oswald:wght@600&display=swap">
<style>
  :root {
    --stage: #dedede;
    --card-black: #0c0c0c;
    --card-face: #1b1b1b;
    --gold: #d9a521;
    --gold-light: #f3d36b;
    --gold-deep: #8a6410;
  }
  * { box-sizing: border-box; margin: 0; padding: 0; }
  html, body { width: 1200px; height: 958px; overflow: hidden; }
  body {
    background: var(--stage);
    position: relative;
  }
  .card {
    position: absolute;
    top: 159px;
    width: 457px;
    height: 640px;
    border-radius: 26px;
    background: var(--card-black);
  }
  .card--back { left: 120px; }
  .card--face { left: 623px; background: linear-gradient(160deg, var(--card-face), var(--card-black)); }

  .card__frame {
    position: absolute;
    inset: 16px;
    border: 3px solid var(--gold);
    border-radius: 18px;
  }
  .card__frame--inner {
    inset: 26px;
    border-width: 1.5px;
    border-radius: 12px;
  }

  .back__pattern {
    position: absolute;
    inset: 26px;
    border-radius: 12px;
    background: radial-gradient(ellipse at 50% 45%, var(--gold-light), var(--gold) 45%, var(--gold-deep) 100%);
  }
  .back__plaque {
    position: absolute;
    left: 50%;
    top: 50%;
    transform: translate(-50%, -50%);
    padding: 14px 30px;
    background: var(--card-black);
    border: 3px solid var(--gold);
    border-radius: 10px;
  }
  .brand-name {
    font-family: "Oswald", sans-serif;
    font-weight: 600;
    font-size: 34px;
    letter-spacing: 1px;
    color: var(--gold);
    white-space: nowrap;
    text-transform: uppercase;
  }

  .index {
    position: absolute;
    display: flex;
    flex-direction: column;
    align-items: center;
    color: var(--gold);
  }
  .index--top { top: 42px; left: 44px; }
  .index--bottom { bottom: 42px; right: 44px; transform: rotate(180deg); }
  .index__rank {
    font-family: "Alfa Slab One", serif;
    font-size: 46px;
    line-height: 1;
  }
  .index__suit { width: 28px; height: 30px; margin-top: 4px; }

  .face__pip {
    position: absolute;
    left: 50%;
    top: 50%;
    width: 230px;
    height: 260px;
    transform: translate(-50%, -50%);
  }
</style>
</head>
<body>

  <section class="card card--back" aria-label="Card back">
    <div class="card__frame"></div>
    <div class="back__pattern" role="img" aria-label="Gold ornamental paisley and leaf pattern"></div>
    <div class="back__plaque">
      <span class="brand-name">Kettleby Twins</span>
    </div>
  </section>

  <section class="card card--face" aria-label="Ace of spades">
    <div class="card__frame"></div>
    <div class="card__frame card__frame--inner"></div>

    <div class="index index--top">
      <span class="index__rank">A</span>
      <svg class="index__suit" viewBox="0 0 28 30" aria-hidden="true">
        <path fill="currentColor" d="M14 0C10 7 1 11 1 18c0 4 3 7 7 7 2 0 4-1 5-3-.5 3-2 6-4 8h10c-2-2-3.5-5-4-8 1 2 3 3 5 3 4 0 7-3 7-7C27 11 18 7 14 0z"/>
      </svg>
    </div>

    <svg class="face__pip" viewBox="0 0 230 260" role="img" aria-label="Ornate gold paisley spade illustration">
      <defs>
        <linearGradient id="pipGold" x1="0" y1="0" x2="1" y2="1">
          <stop offset="0" stop-color="#f3d36b"/>
          <stop offset="0.55" stop-color="#d9a521"/>
          <stop offset="1" stop-color="#8a6410"/>
        </linearGradient>
      </defs>
      <path fill="url(#pipGold)" d="M115 0C85 55 5 85 5 150c0 36 28 60 60 60 20 0 36-9 45-24-3 30-16 52-40 74h90c-24-22-37-44-40-74 9 15 25 24 45 24 32 0 60-24 60-60C225 85 145 55 115 0z"/>
    </svg>

    <div class="index index--bottom">
      <span class="index__rank">A</span>
      <svg class="index__suit" viewBox="0 0 28 30" aria-hidden="true">
        <path fill="currentColor" d="M14 0C10 7 1 11 1 18c0 4 3 7 7 7 2 0 4-1 5-3-.5 3-2 6-4 8h10c-2-2-3.5-5-4-8 1 2 3 3 5 3 4 0 7-3 7-7C27 11 18 7 14 0z"/>
      </svg>
    </div>
  </section>

</body>
</html>
```